Heritage Hollow Business Cards

Require a business card design. <br/><br/>Needs to include logo (either round or long version) plus these details:<br/>Maya Torvell<br/>Heritage Hollow<br/>maya@kelvadtrading.com.au<br/>02 6481 7395<br/>PO Box Glenwarra NSW 2791<br/>www.heritagehollow.com.au<br/><br/>I need in an editable format so that I can create for multiple staff members. <br/><br/>

Target Market(s)

We are an online store selling renovation products to home owners are builders. Looking for a classic classy design.

Industry/Entity Type

Home And Garden

Contact Information for Business Card

Maya Torvell
Heritage Hollow
maya@kelvadtrading.com.au
02 6481 7395
PO Box Glenwarra NSW 2791
www.heritagehollow.com.au

Colors

Designer to choose colors to be used in the design.

Requirements
Must have
• Must include Logo.

```html
<!DOCTYPE html>
<html lang="en">
<head>
<meta charset="utf-8">
<title>Heritage Hollow Business Cards</title>
<link href="https://fonts.googleapis.com/css2?family=Arimo:wght@400;700&display=swap" rel="stylesheet">
<style>
  :root {
    --backdrop: #1d1d1d;
    --card-white: #ffffff;
    --panel-dark: #2a2627;
    --accent-yellow: #f8b517;
    --ink: #1c1c1c;
    --ink-soft: #333333;
    --logo-light: #f2f2f2;
  }
  * { margin: 0; padding: 0; box-sizing: border-box; }
  html, body {
    width: 1200px; height: 900px; overflow: hidden;
    background: var(--backdrop);
    font-family: "Arimo", Arial, sans-serif;
  }
  .card-sheet {
    position: relative; width: 1200px; height: 900px;
    display: flex; flex-direction: column; align-items: center;
    justify-content: center; gap: 40px;
  }
  .card {
    position: relative; width: 700px; height: 400px;
    background: var(--card-white); overflow: hidden;
    box-shadow: 0 10px 30px rgba(0,0,0,0.5);
  }

  /* Front card */
  .card-front { display: flex; }
  .brand-panel {
    width: 280px; height: 100%;
    background: var(--panel-dark);
    display: flex; align-items: center; justify-content: center;
  }
  .brand-name {
    font-weight: 700; font-size: 30px; line-height: 1.05;
    color: var(--logo-light); text-align: center;
  }
  .details-panel { flex: 1; position: relative; padding: 60px 40px 0 50px; }
  .person { display: flex; align-items: flex-start; gap: 16px; }
  .person-icon { width: 18px; height: 22px; margin-top: 16px; }
  .person-name { font-size: 26px; color: var(--ink); letter-spacing: 0.5px; }
  .person-name strong { font-weight: 700; }
  .person-company { font-size: 16px; color: var(--ink-soft); margin-top: 4px; }
  .contact-list {
    list-style: none; position: absolute; left: 50px; bottom: 70px;
    display: flex; flex-direction: column; gap: 16px;
  }
  .contact-item {
    display: flex; align-items: center; gap: 18px;
    font-size: 16px; color: var(--ink); letter-spacing: 0.3px;
  }
  .contact-icon { width: 16px; height: 16px; flex-shrink: 0; }

  /* Back card */
  .card-back { display: flex; flex-direction: column; align-items: center; justify-content: center; }
  .accent-bar { position: absolute; height: 34px; background: var(--accent-yellow); }
  .accent-bar-top { right: 0; top: 70px; width: 180px; }
  .accent-bar-bottom { left: 0; bottom: 70px; width: 200px; }
  .back-brand {
    font-weight: 700; font-size: 42px; line-height: 1.05;
    color: var(--ink); text-align: center;
  }
  .website { margin-top: 60px; font-size: 18px; color: var(--ink); letter-spacing: 0.5px; }
</style>
</head>
<body>
<main class="card-sheet">

  <section class="card card-front" aria-label="Business card front">
    <div class="brand-panel">
      <p class="brand-name">Heritage<br>Hollow</p>
    </div>
    <div class="details-panel">
      <div class="person">
        <svg class="person-icon" viewBox="0 0 18 22" aria-hidden="true">
          <circle cx="9" cy="5" r="4" fill="var(--accent-yellow)"/>
          <path d="M1 21 C1 13 17 13 17 21 Z" fill="var(--accent-yellow)"/>
        </svg>
        <div>
          <p class="person-name"><strong>Maya</strong> Torvell</p>
          <p class="person-company">Heritage Hollow</p>
        </div>
      </div>
      <ul class="contact-list">
        <li class="contact-item">
          <svg class="contact-icon" viewBox="0 0 16 16" aria-hidden="true">
            <path d="M3 1 L6 1 L7 5 L5 6.5 C6 9 7 10 9.5 11 L11 9 L15 10 L15 13 C15 14 14 15 13 15 C6 15 1 10 1 3 C1 2 2 1 3 1 Z" fill="var(--accent-yellow)"/>
          </svg>
          <span>02 6481 7395</span>
        </li>
        <li class="contact-item">
          <svg class="contact-icon" viewBox="0 0 16 16" aria-hidden="true">
            <rect x="1" y="3" width="14" height="10" fill="var(--accent-yellow)"/>
            <path d="M1 3 L8 9 L15 3" fill="none" stroke="#fff" stroke-width="1.3"/>
          </svg>
          <span>maya@kelvadtrading.com.au</span>
        </li>
        <li class="contact-item">
          <svg class="contact-icon" viewBox="0 0 16 16" aria-hidden="true">
            <path d="M8 1 L15 8 L13 8 L13 15 L9.5 15 L9.5 10.5 L6.5 10.5 L6.5 15 L3 15 L3 8 L1 8 Z" fill="var(--accent-yellow)"/>
          </svg>
          <span>PO Box Glenwarra NSW 2791</span>
        </li>
      </ul>
    </div>
  </section>

  <section class="card card-back" aria-label="Business card back">
    <div class="accent-bar accent-bar-top"></div>
    <div class="accent-bar accent-bar-bottom"></div>
    <p class="back-brand">Heritage<br>Hollow</p>
    <p class="website">www.heritagehollow.com.au</p>
  </section>

</main>
</body>
</html>
```